Construction company business card

One side to be the logo with the company name, The other side I would like: (Tomas verbick) Project manager 41 barrow crescent kelvale 52917306224783(03) 9703 2428Info@gudeljgroup.comAnd then maybe a couple dot points saying what we do:Construction (commercial & industrial) Civil construction

Anything else please contact me!
Maybe curved st one edge of the card

Target Market(s)

Older clientele

Industry/Entity Type

Construction Company

Contact Information for Business Card

Read above

Colors
3277b5
1b1b1b
9d9d9d

Requirements
Must have
• Use my logo on one side
Nice to have
• Read above
Should not have
• Read above

```html
<!DOCTYPE html>
<html lang="en">
<head>
<meta charset="utf-8">
<title>Stonefield Property Group – Business Card</title>
<link rel="stylesheet" href="https://fonts.googleapis.com/css2?family=Lato:wght@400;700;900&display=swap">
<style>
  :root {
    --brand-blue: #3277b5;
    --brand-dark: #1b1b1b;
    --brand-grey: #9d9d9d;
    --card-dark: #262626;
    --card-light: #f3f3f3;
    --text-body: #4a4a4a;
    --rule: #d9d9d9;
    --backdrop: #5a5a5a;
  }
  * { margin: 0; padding: 0; box-sizing: border-box; }
  html, body { width: 1200px; height: 900px; overflow: hidden; }
  body {
    background: var(--backdrop);
    font-family: "Lato", Arial, sans-serif;
    position: relative;
  }
  .card {
    position: absolute;
    top: 200px;
    width: 310px;
    height: 502px;
  }
  .card--front {
    left: 253px;
    background: var(--card-light);
    border-radius: 62px 0 62px 0;
  }
  .card--back {
    left: 627px;
    background: var(--card-dark);
    border-radius: 0 62px 0 62px;
  }
  .wordmark {
    color: var(--brand-blue);
    font-weight: 900;
    text-transform: uppercase;
    line-height: 1;
    white-space: nowrap;
  }
  .card--front .wordmark {
    position: absolute;
    left: 34px;
    top: 124px;
    font-size: 31px;
    letter-spacing: 3.4px;
  }
  .wordmark__sub {
    display: block;
    font-size: 13px;
    font-weight: 900;
    letter-spacing: 6.4px;
    margin-top: 4px;
  }
  .person {
    position: absolute;
    left: 34px;
    top: 240px;
  }
  .person__name {
    color: var(--brand-blue);
    font-size: 19px;
    font-weight: 400;
    text-transform: uppercase;
    letter-spacing: 0.2px;
  }
  .person__role {
    color: var(--text-body);
    font-size: 14px;
    margin-top: 1px;
  }
  .contact {
    position: absolute;
    left: 33px;
    top: 294px;
    list-style: none;
    color: var(--text-body);
    font-size: 14px;
    line-height: 18px;
  }
  .contact li { display: flex; align-items: flex-start; }
  .contact .contact__address { margin-top: 9px; }
  .contact svg { width: 12px; height: 12px; margin: 3px 4px 0 0; flex: none; fill: var(--brand-blue); }
  .divider {
    position: absolute;
    left: 34px;
    top: 407px;
    width: 178px;
    height: 1px;
    background: var(--rule);
  }
  .services {
    position: absolute;
    left: 34px;
    top: 417px;
    list-style: none;
    color: var(--text-body);
    font-size: 14px;
    line-height: 18px;
  }
  .services li { position: relative; padding-left: 11px; }
  .services li::before {
    content: "";
    position: absolute;
    left: 0;
    top: 5px;
    width: 8px;
    height: 8px;
    border-radius: 50%;
    background: var(--brand-blue);
  }
  .back-mark {
    position: absolute;
    left: 0;
    right: 0;
    top: 162px;
    display: flex;
    flex-direction: column;
    align-items: center;
  }
  .back-mark__dot {
    width: 118px;
    height: 118px;
    border-radius: 50%;
    background: var(--brand-blue);
  }
  .card--back .wordmark {
    margin-top: 20px;
    font-size: 31px;
    text-align: center;
    letter-spacing: 3.4px;
  }
  .card--back .wordmark__sub { letter-spacing: 6.4px; }
</style>
</head>
<body>
  <section class="card card--front" aria-label="Card front">
    <div class="wordmark">Stonefield<span class="wordmark__sub">Property Group</span></div>

    <div class="person">
      <h1 class="person__name">Tomas Verbick</h1>
      <p class="person__role">Project manager</p>
    </div>

    <ul class="contact">
      <li>
        <svg viewBox="0 0 12 12" aria-hidden="true"><path d="M1 4c0-1.5 2.2-3 5-3s5 1.5 5 3l-2 .8L8 3.4H4L3 4.8zM2.5 6 4 4.5h4L9.5 6v4.5h-7z"/></svg>
        7306224783
      </li>
      <li>
        <svg viewBox="0 0 12 12" aria-hidden="true"><path d="M3.5 0h5a1 1 0 0 1 1 1v10a1 1 0 0 1-1 1h-5a1 1 0 0 1-1-1V1a1 1 0 0 1 1-1zm.3 1.5v8h4.4v-8zM6 10.2a.6.6 0 1 0 0 1.2.6.6 0 0 0 0-1.2z"/></svg>
        (03) 9418 6573
      </li>
      <li>
        <svg viewBox="0 0 12 12" aria-hidden="true"><path d="M0 2.5h12v7H0zm1 .8L6 7l5-3.7V3.3H1z"/></svg>
        Info@verbickgroup.com
      </li>
      <li class="contact__address">
        <svg viewBox="0 0 12 12" aria-hidden="true"><path d="M6 0a4 4 0 0 1 4 4c0 3-4 8-4 8S2 7 2 4a4 4 0 0 1 4-4zm0 2.4a1.6 1.6 0 1 0 0 3.2 1.6 1.6 0 0 0 0-3.2z"/></svg>
        <span>41 barrow crescent<br>kelvale 5291</span>
      </li>
    </ul>

    <div class="divider"></div>

    <ul class="services">
      <li>Construction<br>(commercial &amp; industrial)</li>
      <li>Civil construction</li>
    </ul>
  </section>

  <section class="card card--back" aria-label="Card back">
    <div class="back-mark">
      <div class="back-mark__dot"></div>
      <div class="wordmark">Stonefield<span class="wordmark__sub">Property Group</span></div>
    </div>
  </section>
</body>
</html>
```